Blind Rivet Product catalogue

Need a design in wordpress with a productcatalogue where i present all products. This is a B2B business. The products is Blindrivets and Blindrivet nuts and accessories to this. I only want the basic information and also technical specification.

This is a subcompany to my existing company k7.m3.se but specializing in a subcategory

Businesses using blind rivet technology.

Industrial

Sans Serif

Must have
• Three different categories for the products; Blind Rivets - Blind Rivet Nut - Riveting Tools
Nice to have
• Possible to ad login for more information of the different sizes

```html
<!DOCTYPE html>
<html lang="en">
<head>
<meta charset="utf-8">
<title>K7M3 – Blind Rivets Catalogue</title>
<link href="https://fonts.googleapis.com/css2?family=Michroma&family=Rubik:wght@400;500&display=swap" rel="stylesheet">
<style>
:root{
  --green:#6bb935;
  --red:#d3121f;
  --black:#000;
  --ink:#333;
  --muted:#666;
  --light:#f4f4f4;
  --line:#e2e2e2;
  --white:#fff;
  --head:"Michroma",sans-serif;
  --body:"Rubik",sans-serif;
}
*{box-sizing:border-box;margin:0;padding:0}
html,body{width:1200px;height:3102px;overflow:hidden}
body{font-family:var(--body);color:var(--ink);position:relative;background:var(--white)}
.abs{position:absolute}
a{color:inherit;text-decoration:none}

/* header */
.site-header{position:absolute;left:0;top:0;width:1200px;height:130px;background:var(--black);border-bottom:3px solid var(--green)}
.brand{position:absolute;left:112px;top:44px;color:var(--white);font:500 34px var(--body);letter-spacing:3px;display:flex;align-items:center;gap:10px}
.brand-dot{width:18px;height:18px;background:var(--green)}
.btn{display:inline-flex;align-items:center;justify-content:center;font:500 14px var(--body);color:var(--white);text-transform:uppercase}
.btn-register{position:absolute;left:828px;top:22px;width:111px;height:36px;background:var(--green)}
.btn-login{position:absolute;left:948px;top:22px;width:96px;height:36px;background:var(--red)}
.cart{position:absolute;left:1056px;top:18px}
.cart-count{position:absolute;left:1063px;top:16px;color:var(--green);font:13px var(--body)}
.main-nav{position:absolute;top:86px;left:309px;display:flex;gap:0;font:500 12.5px var(--body);color:var(--white)}
.main-nav a{margin-right:38px}
.main-nav a.active{color:var(--green)}

/* hero */
.hero{position:absolute;left:0;top:130px;width:1200px;height:695px;background:linear-gradient(100deg,#2a2a2a 0%,#4a4a4a 40%,#6d6a66 60%,#3a3937 100%)}
.hero-title{position:absolute;left:112px;top:200px;font:54px var(--head);color:var(--white);letter-spacing:1px}
.hero-sub{position:absolute;left:112px;top:280px;font:12.5px/26px var(--head);color:var(--white)}
.btn-hero{position:absolute;left:112px;top:349px;width:120px;height:47px;background:var(--green);font-family:var(--head);font-size:12.5px}

/* welcome */
.search-label{left:112px;top:864px;font:500 13px var(--body);color:var(--ink)}
.search-box{left:112px;top:889px;width:238px;height:41px;border:2px solid #ddd;border-radius:3px}
.search-box svg{position:absolute;right:14px;top:12px}
.categories{left:112px;top:951px;width:243px;height:208px;background:var(--green)}
.categories h3{height:57px;padding:20px 0 0 18px;font:17px var(--head);color:var(--white);border-bottom:1px solid #88c95a}
.categories li{list-style:none;height:48px;padding:17px 0 0 18px;font:500 13.5px var(--body);color:var(--white);border-bottom:1px solid #88c95a}
.categories li:last-child{border-bottom:0}
.categories li span{margin-right:8px}
.welcome-title{left:398px;top:860px;font:21px var(--head);color:#222}
.welcome-rule{left:398px;top:902px;width:52px;height:3px;background:var(--green)}
.welcome-text{left:398px;top:922px;width:693px;font:14px/30px var(--body);color:var(--muted)}
.btn-welcome{position:absolute;left:398px;top:1116px;width:109px;height:41px;background:var(--red)}

/* section headings */
.section-head{position:absolute;left:0;width:1200px;text-align:center}
.section-head .marks{display:block;margin:0 auto;width:286px;height:6px;position:relative}
.section-head .marks::before{content:"";position:absolute;left:0;top:2px;width:60px;height:2px;background:var(--green)}
.section-head .marks::after{content:"";position:absolute;left:60px;top:2px;width:226px;height:2px;background:var(--red)}
.section-head h2{font:27px var(--head);color:#222;margin-top:12px}

/* products */
.products{position:absolute;left:0;top:1232px;width:1200px;height:620px;background:var(--light)}
.product-card{position:absolute;top:1378px;width:305px;height:412px;background:var(--white);border:1px solid var(--line);box-shadow:0 2px 6px rgba(0,0,0,.15);text-align:center}
.product-media{position:absolute;left:30px;top:40px;width:245px;height:160px;border-radius:4px}
.stars{position:absolute;left:0;top:220px;width:100%;color:#e88a1a;font-size:13px;letter-spacing:2px}
.product-name{position:absolute;left:0;top:245px;width:100%;font:500 20px var(--body);color:#222}
.product-price{position:absolute;left:0;top:278px;width:100%;font:18px var(--head)}
.btn-view{position:absolute;left:39px;top:326px;width:226px;height:47px;font:500 18px var(--body)}
.is-green{color:var(--green)}.is-red{color:var(--red)}
.bg-green{background:var(--green)}.bg-red{background:var(--red)}

/* about */
.about{position:absolute;left:0;top:1852px;width:1200px;height:424px;background:var(--green);overflow:hidden}
.about-red{position:absolute;inset:0;background:var(--red);clip-path:polygon(0 0,455px 0,595px 50%,455px 100%,0 100%)}
.about-white{position:absolute;inset:0;background:var(--white);clip-path:polygon(0 0,438px 0,575px 50%,438px 100%,0 100%)}
.about-photo{position:absolute;inset:0;background:linear-gradient(120deg,#3b3b3b,#8a8580 45%,#b8a77a 70%,#4a4a4a);clip-path:polygon(0 0,432px 0,567px 50%,432px 100%,0 100%)}
.about-marks{position:absolute;left:630px;top:50px;width:168px;height:2px;background:var(--white)}
.about-title{position:absolute;left:630px;top:62px;font:27px var(--head);color:var(--white)}
.about-text{position:absolute;left:626px;top:124px;width:448px;font:14px/26px var(--body);color:var(--white);text-align:justify}
.about-text p+p{margin-top:26px}

/* news */
.news-card{position:absolute;top:2412px;width:312px;height:220px;border:2px solid var(--line);border-radius:6px;background:var(--white)}
.news-date{position:absolute;left:14px;top:18px;width:80px;height:80px;border-radius:50%;color:var(--white);text-align:center;padding-top:15px;font:22px/26px var(--body)}
.news-date small{display:block;font-size:17px;line-height:22px}
.news-title{position:absolute;left:110px;top:34px;font:500 16px/25px var(--body);color:#444;text-transform:uppercase}
.news-text{position:absolute;left:20px;top:120px;width:280px;font:12px/26px var(--body);color:var(--muted)}

/* footer */
.site-footer{position:absolute;left:0;top:2695px;width:1200px;height:407px;background:var(--black);color:var(--white)}
.footer-brand{position:absolute;left:192px;top:100px;font:500 34px var(--body);letter-spacing:3px;color:var(--white);display:flex;align-items:center;gap:10px}
.social{position:absolute;left:148px;top:207px;display:flex;gap:7px}
.social span{width:36px;height:36px;border:2px solid var(--white);border-radius:50%}
.footer-head{position:absolute;top:52px;font:500 21px var(--head);color:var(--white)}
.quick-links{position:absolute;left:410px;top:93px;list-style:none;font:16px var(--body)}
.quick-links li{height:29px}
.quick-links li span{display:inline-block;width:32px;font-size:14px}
.contact-item{position:absolute;left:598px;display:flex;font:13px/20px var(--body)}
.contact-item svg{width:28px;flex:none;margin-top:3px}
.contact-item div{margin-left:8px}
.newsletter-text{position:absolute;left:858px;top:90px;width:240px;font:15.5px/28px var(--body)}
.newsletter-input{position:absolute;left:858px;top:169px;width:228px;height:45px;background:var(--white);border-radius:3px;color:#444;font:12px var(--body);padding:16px 0 0 18px}
.btn-submit{position:absolute;left:858px;top:228px;width:103px;height:40px;background:var(--green);border-radius:20px;font:500 17px var(--body);text-transform:none}
.footer-rule{position:absolute;left:110px;top:325px;width:976px;height:1px;background:#333}
.copyright{position:absolute;left:112px;top:358px;font:14px var(--body)}
.cards{position:absolute;left:915px;top:356px;display:flex;gap:5px}
.cards span{width:40px;height:24px;border-radius:3px}
.cards-note{position:absolute;left:1098px;top:366px;font:11px var(--body)}
</style>
</head>
<body>

<header class="site-header">
  <a class="brand" href="#"><span class="brand-dot"></span>K7M3</a>
  <a class="btn btn-register" href="#">Register</a>
  <a class="btn btn-login" href="#">Login</a>
  <span class="cart-count">0</span>
  <svg class="cart" width="24" height="32" viewBox="0 0 24 32"><path d="M1 13h4l3 10h11l3-8H7" fill="none" stroke="#fff" stroke-width="2.4"/><path d="M7 15h14l-2 6H9z" fill="#fff"/><circle cx="10" cy="27" r="2" fill="#fff"/><circle cx="18" cy="27" r="2" fill="#fff"/></svg>
  <nav class="main-nav">
    <a class="active" href="#">HOME</a><a href="#">MARIN</a><a href="#">SCREW</a><a href="#">STICKS</a><a href="#">NUTS</a><a href="#">TRAYS</a><a href="#">SCREW PIN</a><a href="#">ABOUT US</a><a href="#" style="margin-right:0">CONTACT US</a>
  </nav>
</header>

<section class="hero" role="img" aria-label="Gloved hands using a riveting gun on an aluminium profile">
  <h1 class="hero-title">BLIND RIVETS</h1>
  <p class="hero-sub">SED UT PERSPICIATIS UNDE OMNIS ISTE NATUS ERROR<br>SIT VOLUPTATEM ACCUSANTIUM DOLOREMQUE</p>
  <a class="btn btn-hero" href="#">READ MORE</a>
</section>

<p class="abs search-label">SEARCH</p>
<div class="abs search-box"><svg width="14" height="14" viewBox="0 0 14 14"><circle cx="6" cy="6" r="4.3" fill="none" stroke="#777" stroke-width="1.8"/><path d="M9 9l4 4" stroke="#777" stroke-width="1.8"/></svg></div>
<aside class="abs categories">
  <h3>CATEGORIES</h3>
  <ul>
    <li><span>»</span>BLIND RIVETS</li>
    <li><span>»</span>BLIND RIVET NUT</li>
    <li><span>»</span>RIVETING TOOLS</li>
  </ul>
</aside>
<h2 class="abs welcome-title">WELCOME TO K7M3</h2>
<div class="abs welcome-rule"></div>
<p class="abs welcome-text">K7M3 sells stainless steel fasteners to stores, retailers and industry. On our site you can find most known DIN and ISO standards in mounting. We also have a large range of Marine products in stainless steel. Welcome to look around our store. You navigate through the menu at the top of the page, if you want to see an overview of all products in a certain category, click on the name. For example, if you move your mouse over screws in the menu and click on wooden screws, all products in that category are displayed. Each item has a packaging size that is also the smallest order item!</p>
<a class="btn btn-welcome" href="#">READ MORE</a>

<section class="products"></section>
<div class="section-head" style="top:1262px"><span class="marks"></span><h2>LATEST PRODUCTS</h2></div>

<article class="product-card" style="left:112px">
  <div class="product-media" role="img" aria-label="Stainless blind rivet" style="background:radial-gradient(ellipse at center,#e2e2e2,#fff 70%)"></div>
  <div class="stars">☆☆☆☆☆</div>
  <h3 class="product-name">BLIND RIVETS</h3>
  <p class="product-price is-green">24,25 KR</p>
  <a class="btn btn-view bg-green" href="#">VIEW DEATILS</a>
</article>
<article class="product-card" style="left:448px">
  <div class="product-media" role="img" aria-label="Stainless blind rivet nut" style="background:radial-gradient(ellipse at center,#d6d6d6,#fff 70%)"></div>
  <div class="stars">☆☆☆☆☆</div>
  <h3 class="product-name">BLIND RIVET NUT</h3>
  <p class="product-price is-red">57,38 KR</p>
  <a class="btn btn-view bg-red" href="#">VIEW DEATILS</a>
</article>
<article class="product-card" style="left:784px">
  <div class="product-media" role="img" aria-label="Cordless riveting tool" style="background:radial-gradient(ellipse at center,#bfc3c8,#fff 70%)"></div>
  <div class="stars">☆☆☆☆☆</div>
  <h3 class="product-name">RIVETING TOOLS</h3>
  <p class="product-price is-green">235,67 KR</p>
  <a class="btn btn-view bg-green" href="#">VIEW DEATILS</a>
</article>

<section class="about">
  <div class="about-red"></div>
  <div class="about-white"></div>
  <div class="about-photo" role="img" aria-label="Hand fitting a fastener into an engine block"></div>
  <div class="about-marks"></div>
  <h2 class="about-title">ABOUT US</h2>
  <div class="about-text">
    <p>K7M3 AB is a wholesale company that caters to other companies. Our range consists of stainless steel products for mounting and marine applications. We have the widest and deepest range of stainless steel on the market. Our attachments comply with DIN standards and ISO standards.</p>
    <p>Please note that we only sell unbroken packaging. The minimum order quantity per pack can be found at the bottom left of each product. We also reserve the right to change the packaging size to the one our supplier sends.</p>
  </div>
</section>

<div class="section-head" style="top:2316px"><span class="marks" style="width:222px"></span><h2>LATEST NEWS</h2></div>

<article class="news-card" style="left:112px">
  <div class="news-date bg-red">04<small>Mar</small></div>
  <h3 class="news-title">Sed ut perspiciatis<br>unde omnis</h3>
  <p class="news-text">Nemo enim ipsam voluptatem quia voluptas sit asp ernatur aut odit aut fugit, sed quia consequu ntura magni dolores eos qui ratione</p>
</article>
<article class="news-card" style="left:445px">
  <div class="news-date bg-green">04<small>Mar</small></div>
  <h3 class="news-title">Sed ut perspiciatis<br>unde omnis</h3>
  <p class="news-text">Nemo enim ipsam voluptatem quia voluptas sit asp ernatur aut odit aut fugit, sed quia consequu ntura magni dolores eos qui ratione</p>
</article>
<article class="news-card" style="left:778px">
  <div class="news-date bg-red">04<small>Mar</small></div>
  <h3 class="news-title">Sed ut perspiciatis<br>unde omnis</h3>
  <p class="news-text">Nemo enim ipsam voluptatem quia voluptas sit asp ernatur aut odit aut fugit, sed quia consequu ntura magni dolores eos qui ratione</p>
</article>

<footer class="site-footer">
  <div class="footer-brand"><span class="brand-dot"></span>K7M3</div>
  <div class="social" aria-label="Social links"><span></span><span></span><span></span><span></span><span></span></div>

  <h3 class="footer-head" style="left:407px">Quick Links</h3>
  <ul class="quick-links">
    <li><span>»</span>Home</li><li><span>»</span>Marin</li><li><span>»</span>Screw</li><li><span>»</span>sticks</li><li><span>»</span>nuts</li><li><span>»</span>trays</li><li><span>»</span>Screw Pin</li>
  </ul>

  <h3 class="footer-head" style="left:598px;top:55px">Contact Us</h3>
  <div class="contact-item" style="top:93px">
    <svg height="16" viewBox="0 0 12 16"><path d="M6 0a5 5 0 0 0-5 5c0 4 5 11 5 11s5-7 5-11a5 5 0 0 0-5-5zm0 7a2 2 0 1 1 0-4 2 2 0 0 1 0 4z" fill="#fff"/></svg>
    <div>Address :<br>#15 Lorem Ipsum Dummy<br>Lorem Ipsum Dummy</div>
  </div>
  <div class="contact-item" style="top:180px">
    <svg height="16" viewBox="0 0 16 16"><path d="M3 1l3 3-2 2c1 2 4 5 6 6l2-2 3 3-2 2C7 15 1 9 1 3z" fill="#fff"/></svg>
    <div>Phone :<br>000-121-1231</div>
  </div>
  <div class="contact-item" style="top:242px">
    <svg height="14" viewBox="0 0 16 12"><rect x="0" y="0" width="16" height="12" fill="#fff"/><path d="M0 0l8 6 8-6" fill="none" stroke="#000" stroke-width="1.5"/></svg>
    <div>Email :<br>info@fastenerdesk.com</div>
  </div>

  <h3 class="footer-head" style="left:858px">Newsletter</h3>
  <p class="newsletter-text">Sed ut perspiciatis unde omnis natus error sit voluptatem</p>
  <div class="newsletter-input">Enter Email Id :</div>
  <a class="btn btn-submit" href="#">Submit</a>

  <div class="footer-rule"></div>
  <p class="copyright">© Copyright 2020 K7M3.All Rights Reserved</p>
  <div class="cards" aria-label="Accepted payment cards">
    <span style="background:#dfe6f2"></span><span style="background:#f2c98a"></span><span style="background:#bcd7ef"></span><span style="background:#e8e8e8"></span>
  </div>
  <span class="cards-note">C2</span>
</footer>

</body>
</html>
```